Business Card Design for Training Business

Clear Path Coaching is a new business that delivers training and other services with a focus on topics related to mental health and wellbeing, for example, Wellmind Response Course, Resilience etc. We have a strong focus on evidence-based psychology and neuroscience. I have a logo which I will upload with the brief, so please consider colours that work well with the logo.
Target Market(s)
Adults, workplaces (particularly government and not-for-profits)
Industry/Entity Type
Business
Contact Information for Business Card
Head Strong TrainingSamantha SellwoodDirector0438 770 850sam@headstrongtraining.com.auwww.headstrongtraining.com.au

```html
<!DOCTYPE html>
<html lang="en">
<head>
<meta charset="utf-8">
<title>Clear Path Coaching — Business Card</title>
<link rel="stylesheet" href="https://fonts.googleapis.com/css2?family=Questrial&display=swap">
<style>
  :root {
    --backdrop: #363636;
    --card-white: #f6f6f6;
    --teal: #22b5bb;
    --teal-deep: #1fa9ae;
    --ring-brown: #4f403b;
    --ink-grey: #6b6b6b;
    --white: #ffffff;
  }
  * { margin: 0; padding: 0; box-sizing: border-box; }
  html, body {
    width: 1200px; height: 750px; overflow: hidden;
    background: var(--backdrop);
    font-family: "Questrial", "Century Gothic", sans-serif;
  }
  .stage { position: relative; width: 1200px; height: 750px; }

  .card {
    position: absolute; left: 371px; width: 461px; height: 263px;
    overflow: hidden;
    box-shadow: 0 4px 10px rgba(0,0,0,0.45);
  }
  .card--front { top: 106px; background: var(--card-white); }
  .card--back { top: 387px; background: var(--teal); }

  .front-disc { position: absolute; left: 0; top: 0; }

  .contact {
    position: absolute; left: 24px; top: 150px; color: var(--white);
  }
  .contact__name { font-size: 18px; line-height: 1; letter-spacing: 0.2px; }
  .contact__role { font-size: 13px; margin-top: 5px; }
  .contact__list { list-style: none; margin-top: 14px; }
  .contact__item {
    display: flex; align-items: center; gap: 6px;
    font-size: 11.5px; line-height: 17.6px;
  }
  .contact__icon { width: 12px; height: 12px; flex: none; }

  .brand {
    position: absolute; left: 254px; top: 34px; width: 200px;
    display: flex; flex-direction: column; align-items: center;
    color: var(--ink-grey);
  }
  .brand__dot {
    width: 62px; height: 62px; border-radius: 50%;
    border: 2px solid var(--teal);
  }
  .brand__name { margin-top: 16px; font-size: 19px; letter-spacing: 2.4px; line-height: 1; }
  .brand__sub { margin-top: 6px; font-size: 9.5px; letter-spacing: 4px; line-height: 1; }

  .back-brand {
    position: absolute; left: 0; top: 76px; width: 100%;
    display: flex; flex-direction: column; align-items: center; color: var(--white);
  }
  .back-brand__dot {
    width: 110px; height: 110px; border-radius: 50%;
    border: 1.5px solid var(--white);
    display: flex; align-items: center; justify-content: center;
    font-size: 12px; letter-spacing: 2px; text-align: center; line-height: 1.5;
  }
  .back-url {
    position: absolute; left: 0; bottom: 42px; width: 100%;
    text-align: center; color: var(--white); font-size: 12.5px;
  }
</style>
</head>
<body>
<main class="stage">
  <section class="card card--front" aria-label="Business card front">
    <svg class="front-disc" width="461" height="263" viewBox="0 0 461 263" aria-hidden="true">
      <circle cx="126" cy="224" r="147" fill="none" stroke="var(--ring-brown)" stroke-width="3"/>
      <circle cx="126" cy="224" r="142" fill="var(--teal)"/>
    </svg>

    <div class="contact">
      <p class="contact__name">Rebecca Tanfield</p>
      <p class="contact__role">Director</p>
      <ul class="contact__list">
        <li class="contact__item">
          <svg class="contact__icon" viewBox="0 0 24 24" aria-hidden="true"><path fill="#fff" d="M6.6 10.8a15.1 15.1 0 0 0 6.6 6.6l2.2-2.2c.3-.3.7-.4 1-.2 1.1.4 2.3.6 3.6.6.6 0 1 .4 1 1V20c0 .6-.4 1-1 1A17 17 0 0 1 3 4c0-.6.4-1 1-1h3.5c.6 0 1 .4 1 1 0 1.3.2 2.5.6 3.6.1.3 0 .7-.2 1z"/></svg>
          <span>0491 362 517</span>
        </li>
        <li class="contact__item">
          <svg class="contact__icon" viewBox="0 0 24 24" aria-hidden="true"><rect x="2" y="5" width="20" height="14" fill="#fff"/><path d="M2 5l10 8 10-8" fill="none" stroke="var(--teal)" stroke-width="1.6"/></svg>
          <span>bec@clearpathcoaching.example.au</span>
        </li>
        <li class="contact__item">
          <svg class="contact__icon" viewBox="0 0 24 24" aria-hidden="true"><circle cx="12" cy="12" r="10" fill="#fff"/><path d="M12 2v20M2 12h20M12 2c-4 4-4 16 0 20M12 2c4 4 4 16 0 20" fill="none" stroke="var(--teal)" stroke-width="1.4"/></svg>
          <span>www.clearpathcoaching.example.au</span>
        </li>
      </ul>
    </div>

    <div class="brand">
      <div class="brand__dot"></div>
      <p class="brand__name">CLEAR PATH</p>
      <p class="brand__sub">COACHING</p>
    </div>
  </section>

  <section class="card card--back" aria-label="Business card back">
    <div class="back-brand">
      <div class="back-brand__dot">CLEAR PATH<br>COACHING</div>
    </div>
    <p class="back-url">www.clearpathcoaching.example.au</p>
  </section>
</main>
</body>
</html>
```